Business Card Design

We are a residential half way house for the addict ,the alcoholic and dual diagnosed in recovery.
i house both men and woman age 18+

Industry/Entity Type

Residential

```html
<!DOCTYPE html>
<html lang="en">
<head>
<meta charset="utf-8">
<title>Marlowe's Family Sober House – Business Card</title>
<link href="https://fonts.googleapis.com/css2?family=Archivo:wdth,wght@75,900&family=Roboto+Condensed:wght@300;400&display=swap" rel="stylesheet">
<style>
  :root {
    --backdrop: #dcd7d0;
    --card-white: #f7f7f5;
    --ink: #111111;
    --panel-black: #050505;
    --accent-red: #e23a4a;
    --accent-red-light: #ef5563;
    --text-light: #ffffff;
  }
  html, body {
    margin: 0;
    width: 1200px;
    height: 892px;
    overflow: hidden;
    background: var(--backdrop);
  }
  .canvas {
    position: relative;
    width: 1200px;
    height: 892px;
  }
  .card {
    position: absolute;
    left: 100px;
    top: 160px;
    width: 1000px;
    height: 572px;
    background: var(--card-white);
    box-shadow: 0 10px 30px rgba(0,0,0,0.25);
    overflow: hidden;
  }
  .card-panels {
    position: absolute;
    inset: 0;
  }
  .company {
    position: absolute;
    left: 100px;
    top: 50px;
    margin: 0;
    font-family: "Archivo", "Arial Black", sans-serif;
    font-stretch: 75%;
    font-weight: 900;
    color: var(--ink);
    line-height: 1;
  }
  .company-name {
    display: block;
    font-size: 68px;
  }
  .company-type {
    display: block;
    font-size: 46px;
    margin-top: 2px;
    margin-left: 80px;
  }
  .address {
    position: absolute;
    left: 290px;
    top: 214px;
    margin: 0;
    font-family: "Roboto Condensed", "Arial Narrow", sans-serif;
    font-weight: 300;
    font-size: 25px;
    color: var(--ink);
  }
  .contacts {
    position: absolute;
    left: 165px;
    top: 330px;
    margin: 0;
    padding: 0;
    list-style: none;
  }
  .contact-item {
    display: flex;
    align-items: center;
    height: 46px;
    font-family: "Roboto Condensed", "Arial Narrow", sans-serif;
    font-weight: 400;
    font-size: 28px;
    color: var(--text-light);
  }
  .contact-icon {
    width: 28px;
    height: 28px;
    margin-right: 22px;
    flex: none;
  }
  .owner {
    position: absolute;
    right: 40px;
    top: 322px;
    text-align: right;
    font-family: "Roboto Condensed", "Arial Narrow", sans-serif;
    color: var(--ink);
  }
  .owner-name {
    margin: 0;
    font-weight: 300;
    font-size: 42px;
    line-height: 1;
  }
  .owner-role {
    margin: 6px 0 0;
    font-weight: 300;
    font-size: 20px;
  }
  .owner-note {
    margin: 2px 0 0;
    font-weight: 300;
    font-size: 20px;
  }
</style>
</head>
<body>
<div class="canvas">
  <div class="card">
    <svg class="card-panels" width="1000" height="572" viewBox="0 0 1000 572" aria-hidden="true">
      <defs>
        <linearGradient id="redPanel" x1="0" y1="0" x2="1" y2="1">
          <stop offset="0" stop-color="var(--accent-red-light)"/>
          <stop offset="1" stop-color="var(--accent-red)"/>
        </linearGradient>
      </defs>
      <polygon class="panel-black" points="0,298 490,298 680,572 0,572" fill="var(--panel-black)"/>
      <polygon class="panel-red" points="512,298 1000,298 1000,572 702,572" fill="url(#redPanel)"/>
    </svg>

    <h1 class="company">
      <span class="company-name">Marlowe's</span>
      <span class="company-type">Family Sober House Inc</span>
    </h1>
    <p class="address">2418 Palmetto Rd. Lake Haven,Fla 33400</p>

    <ul class="contacts">
      <li class="contact-item">
        <svg class="contact-icon" viewBox="0 0 30 30" aria-hidden="true">
          <rect width="30" height="30" rx="5" fill="var(--accent-red)"/>
          <path d="M9 7c1-1 2-1 3 0l2 3c.6 1 .3 1.8-.4 2.4l-1 .8c.8 1.8 2.3 3.3 4.1 4.1l.8-1c.6-.7 1.4-1 2.4-.4l3 2c1 1 1 2 0 3l-1.5 1.5C19 25 5 11 7.5 8.5Z" fill="var(--panel-black)"/>
        </svg>
        (555) 310-0305
      </li>
      <li class="contact-item">
        <svg class="contact-icon" viewBox="0 0 30 30" aria-hidden="true">
          <rect width="30" height="30" rx="5" fill="var(--accent-red)"/>
          <path d="M9 7c1-1 2-1 3 0l2 3c.6 1 .3 1.8-.4 2.4l-1 .8c.8 1.8 2.3 3.3 4.1 4.1l.8-1c.6-.7 1.4-1 2.4-.4l3 2c1 1 1 2 0 3l-1.5 1.5C19 25 5 11 7.5 8.5Z" fill="var(--panel-black)"/>
        </svg>
        (555) 310-0306
      </li>
      <li class="contact-item">
        <svg class="contact-icon" viewBox="0 0 30 30" aria-hidden="true">
          <rect width="30" height="30" rx="5" fill="var(--accent-red)"/>
          <rect x="10" y="6" width="10" height="6" fill="none" stroke="var(--panel-black)" stroke-width="2"/>
          <rect x="6" y="11" width="18" height="10" rx="2" fill="var(--panel-black)"/>
          <rect x="10" y="17" width="10" height="7" fill="var(--panel-black)" stroke="var(--accent-red)" stroke-width="1.5"/>
        </svg>
        (555) 748-2291
      </li>
      <li class="contact-item">
        <svg class="contact-icon" viewBox="0 0 30 30" aria-hidden="true">
          <rect width="30" height="30" rx="5" fill="var(--accent-red)"/>
          <rect x="6" y="9" width="18" height="12" fill="var(--panel-black)"/>
          <path d="M6 9l9 7 9-7" fill="none" stroke="var(--accent-red)" stroke-width="1.5"/>
        </svg>
        renatavasquez@mailbox.com
      </li>
    </ul>

    <div class="owner">
      <p class="owner-name">Renata Vasquez</p>
      <p class="owner-role">Owner</p>
      <p class="owner-note">(15 yrs.in recovery)</p>
    </div>
  </div>
</div>
</body>
</html>
```